Etiketten für Honig
Wir können nur volle Punktzahl geben. Roswitha ist selbst Ideenreich, wirklich nett und setzte unsere Ideen schnell und engagiert um. Hat echt Spass gemacht mit ihr zu arbeiten.
Zielgruppe
Es scheint Missverständnisse zu geben weshalb ich das Briefing wohl ändern muss.
see below for English translation
Wir sind eine kleine Imkerei, die von der Liebhaberei in den Nebenerwerb wechselt. Wir verkaufen verschiedene Sortenhonige und Honigzubereitungen (siehe Webseite) im vorwiegend ländlichen Raum des Münsterlandes.
Entsprechend unseres Standortes und unserer Kundschaft benötigen wir ein klassisch ländliches Design. Hierfür haben wir auch bereits ein Logo welches verwendet werden muss.
English
There seems to be some misunderstanding, so I guess I'll have to change the briefing.
We are a small apiary that changes from hobby to sideline. We sell different types of honey and honey preparations (e.g. honey with raspberry) in a predominantly rural area of the Münsterland (Muensterland).
According to our location and our clientele, we need a classic rural design. We already have a logo which must be used.
Aufgabenstellung
Wir möchten ein rechteckiges Etikett mit Gewährverschluss das für verschiedene Sorten adoptierbar ist. Zum Beispiel durch den Austausch der Sortenbezeichnung und eine farbliche Veränderung.
Das Design soll später auf Naturpapier oder Graspapier gedruckt werden. Das Logo muss auf Etikett und Gewährverschluss abgebildet werden.
We would like a rectangular label with a guarantee seal that is adoptable for different varieties. For example, by exchanging the variety designation and changing the color.
The design will later be printed on uncoated paper or grass paper. The logo must be shown on the label and guarantee seal.

```html
<!DOCTYPE html>
<html lang="de">
<head>
<meta charset="utf-8">
<title>Honigetiketten mit Siegel</title>
<link href="https://fonts.googleapis.com/css2?family=Montserrat:wght@400;600;700&family=Kaushan+Script&family=Knewave&display=swap" rel="stylesheet">
<style>
  :root{
    --yellow:#f5c518;
    --pale-yellow:#f2d06b;
    --white:#ffffff;
    --paper:#ffffff;
    --ink:#222222;
    --acacia:#7b6a58;
    --blossom:#d585b5;
    --chestnut:#452b1b;
    --forest:#244a21;
    --linden:#c27a12;
    --summer:#0b5355;
    --spring:#8f79b5;
  }
  html,body{margin:0;padding:0}
  body{width:1200px;height:2179px;overflow:hidden;background:var(--paper);position:relative;font-family:"Montserrat",sans-serif}
  .tag{position:absolute;width:444px;height:543px}
  .seal{position:absolute;left:140px;top:42px;width:164px;height:164px;border-radius:50%;background:var(--tone)}
  .seal-face{position:absolute;left:21px;top:21px;width:122px;height:122px;border-radius:50%;background:var(--white);display:flex;align-items:center;justify-content:center}
  .seal-name{font-family:"Montserrat",sans-serif;font-weight:700;font-size:19px;color:var(--tone)}
  .stem{position:absolute;left:196px;top:190px;width:51px;height:180px;background:var(--tone)}
  .label{position:absolute;left:0;top:366px;width:444px;height:178px;background:var(--tone);overflow:hidden}
  .maker{position:absolute;left:11px;top:10px;width:110px;color:var(--yellow)}
  .maker-name{font-weight:700;font-size:17px;line-height:20px}
  .maker-address{margin-top:3px;font-size:5.6px;line-height:7.4px}
  .origin{position:absolute;left:11px;top:96px;width:110px;color:var(--yellow);font-size:5.6px;line-height:7.4px}
  .origin-title{font-family:"Kaushan Script",cursive;font-size:7.5px}
  .best-before{position:absolute;left:9px;top:134px;width:82px;height:34px;background:var(--white);color:var(--ink);font-size:4.6px;font-weight:600;padding:3px;box-sizing:border-box}
  .line-name{position:absolute;left:157px;top:28px;color:var(--yellow);font-weight:600;font-size:11px;letter-spacing:.2px}
  .variety{position:absolute;left:148px;top:40px;width:230px;line-height:1}
  .variety-main{display:block;font-family:"Kaushan Script",cursive;color:var(--white);font-size:46px}
  .variety-sub{display:block;margin:-22px 0 0 36px;font-family:"Knewave",cursive;color:var(--pale-yellow);font-size:36px}
  .variety.single .variety-main{font-size:72px;margin-top:4px}
  .claim{position:absolute;left:178px;top:130px;color:var(--yellow);font-family:"Kaushan Script",cursive;font-size:8px;line-height:9px;transform:rotate(-8deg)}
  .weight{position:absolute;left:252px;top:124px;width:36px;height:36px}
  .weight text{font-family:"Kaushan Script",cursive;font-size:9px;fill:var(--white)}
</style>
</head>
<body>

<section class="tag" style="--tone:var(--acacia);left:142px;top:0">
  <div class="seal"><div class="seal-face"><span class="seal-name">Kerbrink</span></div></div>
  <div class="stem"></div>
  <div class="label">
    <div class="maker"><div class="maker-name">Kerbrink</div><div class="maker-address">Lindenweg 12<br>48000 Heidestadt<br>01234 567890<br>honigmanufaktur-kerbrink.de</div></div>
    <div class="origin"><div class="origin-title">Honig aus Deutschland</div>Trocken, dunkel und vor<br>Wärme geschützt lagern<br>Mehrwegglas</div>
    <div class="best-before">Mindestens haltbar bis:</div>
    <div class="line-name">HEIDEWINKELER LANDHONIG</div>
    <div class="variety"><span class="variety-main">Akazien</span><span class="variety-sub">honig</span></div>
    <div class="claim">Echter Honig aus<br>dem Münsterland!</div>
    <svg class="weight" viewBox="0 0 36 36"><polygon points="18,1 33,9.5 33,26.5 18,35 3,26.5 3,9.5" fill="var(--yellow)"/><text x="18" y="21" text-anchor="middle">500 g</text></svg>
  </div>
</section>

<section class="tag" style="--tone:var(--blossom);left:612px;top:0">
  <div class="seal"><div class="seal-face"><span class="seal-name">Kerbrink</span></div></div>
  <div class="stem"></div>
  <div class="label">
    <div class="maker"><div class="maker-name">Kerbrink</div><div class="maker-address">Lindenweg 12<br>48000 Heidestadt<br>01234 567890<br>honigmanufaktur-kerbrink.de</div></div>
    <div class="origin"><div class="origin-title">Honig aus Deutschland</div>Trocken, dunkel und vor<br>Wärme geschützt lagern<br>Mehrwegglas</div>
    <div class="best-before">Mindestens haltbar bis:</div>
    <div class="line-name">HEIDEWINKELER LANDHONIG</div>
    <div class="variety"><span class="variety-main">Blüten</span><span class="variety-sub">honig</span></div>
    <div class="claim">Echter Honig aus<br>dem Münsterland!</div>
    <svg class="weight" viewBox="0 0 36 36"><polygon points="18,1 33,9.5 33,26.5 18,35 3,26.5 3,9.5" fill="var(--yellow)"/><text x="18" y="21" text-anchor="middle">500 g</text></svg>
  </div>
</section>

<section class="tag" style="--tone:var(--chestnut);left:142px;top:529px">
  <div class="seal"><div class="seal-face"><span class="seal-name">Kerbrink</span></div></div>
  <div class="stem"></div>
  <div class="label">
    <div class="maker"><div class="maker-name">Kerbrink</div><div class="maker-address">Lindenweg 12<br>48000 Heidestadt<br>01234 567890<br>honigmanufaktur-kerbrink.de</div></div>
    <div class="origin"><div class="origin-title">Honig aus Deutschland</div>Trocken, dunkel und vor<br>Wärme geschützt lagern<br>Mehrwegglas</div>
    <div class="best-before">Mindestens haltbar bis:</div>
    <div class="line-name">HEIDEWINKELER LANDHONIG</div>
    <div class="variety"><span class="variety-main">Edel</span><span class="variety-sub" style="margin-left:0">kastanie</span></div>
    <div class="claim">Echter Honig aus<br>dem Münsterland!</div>
    <svg class="weight" viewBox="0 0 36 36"><polygon points="18,1 33,9.5 33,26.5 18,35 3,26.5 3,9.5" fill="var(--yellow)"/><text x="18" y="21" text-anchor="middle">500 g</text></svg>
  </div>
</section>

<section class="tag" style="--tone:var(--forest);left:612px;top:529px">
  <div class="seal"><div class="seal-face"><span class="seal-name">Kerbrink</span></div></div>
  <div class="stem"></div>
  <div class="label">
    <div class="maker"><div class="maker-name">Kerbrink</div><div class="maker-address">Lindenweg 12<br>48000 Heidestadt<br>01234 567890<br>honigmanufaktur-kerbrink.de</div></div>
    <div class="origin"><div class="origin-title">Honig aus Deutschland</div>Trocken, dunkel und vor<br>Wärme geschützt lagern<br>Mehrwegglas</div>
    <div class="best-before">Mindestens haltbar bis:</div>
    <div class="line-name">HEIDEWINKELER LANDHONIG</div>
    <div class="variety"><span class="variety-main">Wald</span><span class="variety-sub">honig</span></div>
    <div class="claim">Echter Honig aus<br>dem Münsterland!</div>
    <svg class="weight" viewBox="0 0 36 36"><polygon points="18,1 33,9.5 33,26.5 18,35 3,26.5 3,9.5" fill="var(--yellow)"/><text x="18" y="21" text-anchor="middle">500 g</text></svg>
  </div>
</section>

<section class="tag" style="--tone:var(--linden);left:142px;top:1058px">
  <div class="seal"><div class="seal-face"><span class="seal-name">Kerbrink</span></div></div>
  <div class="stem"></div>
  <div class="label">
    <div class="maker"><div class="maker-name">Kerbrink</div><div class="maker-address">Lindenweg 12<br>48000 Heidestadt<br>01234 567890<br>honigmanufaktur-kerbrink.de</div></div>
    <div class="origin"><div class="origin-title">Honig aus Deutschland</div>Trocken, dunkel und vor<br>Wärme geschützt lagern<br>Mehrwegglas</div>
    <div class="best-before">Mindestens haltbar bis:</div>
    <div class="line-name">HEIDEWINKELER LANDHONIG</div>
    <div class="variety single" style="left:118px"><span class="variety-main">Linde</span></div>
    <div class="claim">Echter Honig aus<br>dem Münsterland!</div>
    <svg class="weight" viewBox="0 0 36 36"><polygon points="18,1 33,9.5 33,26.5 18,35 3,26.5 3,9.5" fill="var(--yellow)"/><text x="18" y="21" text-anchor="middle">500 g</text></svg>
  </div>
</section>

<section class="tag" style="--tone:var(--summer);left:612px;top:1058px">
  <div class="seal"><div class="seal-face"><span class="seal-name">Kerbrink</span></div></div>
  <div class="stem"></div>
  <div class="label">
    <div class="maker"><div class="maker-name">Kerbrink</div><div class="maker-address">Lindenweg 12<br>48000 Heidestadt<br>01234 567890<br>honigmanufaktur-kerbrink.de</div></div>
    <div class="origin"><div class="origin-title">Honig aus Deutschland</div>Trocken, dunkel und vor<br>Wärme geschützt lagern<br>Mehrwegglas</div>
    <div class="best-before">Mindestens haltbar bis:</div>
    <div class="line-name">HEIDEWINKELER LANDHONIG</div>
    <div class="variety" style="left:128px"><span class="variety-main">Sommer</span><span class="variety-sub">tracht</span></div>
    <div class="claim">Echter Honig aus<br>dem Münsterland!</div>
    <svg class="weight" viewBox="0 0 36 36"><polygon points="18,1 33,9.5 33,26.5 18,35 3,26.5 3,9.5" fill="var(--yellow)"/><text x="18" y="21" text-anchor="middle">500 g</text></svg>
  </div>
</section>

<section class="tag" style="--tone:var(--spring);left:364px;top:1587px">
  <div class="seal"><div class="seal-face"><span class="seal-name">Kerbrink</span></div></div>
  <div class="stem"></div>
  <div class="label">
    <div class="maker"><div class="maker-name">Kerbrink</div><div class="maker-address">Lindenweg 12<br>48000 Heidestadt<br>01234 567890<br>honigmanufaktur-kerbrink.de</div></div>
    <div class="origin"><div class="origin-title">Honig aus Deutschland</div>Trocken, dunkel und vor<br>Wärme geschützt lagern<br>Mehrwegglas</div>
    <div class="best-before">Mindestens haltbar bis:</div>
    <div class="line-name">HEIDEWINKELER LANDHONIG</div>
    <div class="variety"><span class="variety-main">Früh</span><span class="variety-sub">tracht</span></div>
    <div class="claim">Echter Honig aus<br>dem Münsterland!</div>
    <svg class="weight" viewBox="0 0 36 36"><polygon points="18,1 33,9.5 33,26.5 18,35 3,26.5 3,9.5" fill="var(--yellow)"/><text x="18" y="21" text-anchor="middle">500 g</text></svg>
  </div>
</section>

</body>
</html>
```